"Velmora Crest" sexual performance enhancement pill bottle label needed.

This should be interesting...

I am starting a line of sexual performance enhancement products. This will be the first of several products basically. Keep in mind, I am the type of business person to stay with one company for years if they provide me with quality work.

This particular product is a male sexual performance pill. The name of the product is "Velmora Crest." The packaging of the pills are a black bottle with a white top. Label on the product example would be perfect but at a minimum I have attached a "template" for your guidance.

Some of the technical aspects of this are as follows:

-File Format: Illustrator CS6 is preferred. (Winner must provide artwork in layer and can not flatten artwork.)
-Resolution: 300 dpi minimum
-Bleed: 1/16th (0.0625") inch from edge of label
-Color Mode: CMYK only or must be converted to CMYK for final production

Lastly, this is your project as a designer, artist, creator, this is essentially a piece of you that will be sold and known by thousands of people. I have no color scheme that I prefer, just use the template and follow the layout. If you have any further questions, please feel free to contact me at any time.
Updates

Quick note on the product and what it does: -Powerful, long lasting, harder erections -Works in a minutes and last for hours -Enhances sexual desire and drive Thank you for your ideas...

Project Deadline Extended
Reason: We decided to extent the project for a few more days to let the last few concepts come in. So far things are looking really good and we definitely have seen some amazing designs. Thank you for your hard work and amazing creativity. Looking forward to seeing what we have come in the next couple of day. Very respectfully, Brev

ONLY THREE DAYS LEFT!!!! Please submit your ideas as soon as possible. And as always, thank you for your help!!! V/r, Brev

Industry/Entity Type

Graphic Design

```html
<!DOCTYPE html>
<html lang="en">
<head>
<meta charset="utf-8">
<title>Velmora Crest – Label</title>
<link rel="stylesheet" href="https://fonts.googleapis.com/css2?family=Roboto+Condensed:wght@400;700&family=Arimo:wght@700&display=swap">
<style>
  :root {
    --page: #d9d9d9;
    --label: #000000;
    --ink: #ffffff;
    --muted: #d8d8d8;
    --gold: #e9a43a;
    --badge: #d9a21c;
    --glow: #1d4fa8;
  }
  * { box-sizing: border-box; margin: 0; padding: 0; }
  html, body { width: 1022px; height: 1200px; overflow: hidden; }
  body {
    background: var(--page);
    font-family: "Roboto Condensed", Arial, sans-serif;
    color: var(--ink);
    position: relative;
  }
  .label {
    position: absolute;
    left: 71px; top: 426px;
    width: 881px; height: 348px;
    background: var(--label);
    border-radius: 14px;
    overflow: hidden;
  }
  .label > * { position: absolute; }

  /* left panel */
  .directions {
    left: 19px; top: 56px; width: 189px;
    font-size: 6.4px; line-height: 1.3; text-align: justify;
  }
  .directions p { margin-bottom: 4px; }
  .directions p.storage { margin-top: 10px; }
  .fda-note {
    left: 19px; top: 211px; width: 189px; height: 39px;
    border: 1px solid var(--ink);
    padding: 4px 5px;
    font-size: 6.2px; line-height: 1.3;
  }
  .maker {
    left: 22px; top: 265px;
    font-size: 10.5px; line-height: 1.3;
  }

  /* centre panel */
  .hero-art {
    left: 285px; top: 30px; width: 310px; height: 310px;
  }
  .tagline-top {
    left: 280px; width: 320px; top: 50px; text-align: center;
    font-size: 16px;
  }
  .brand-name {
    left: 240px; width: 400px; top: 108px; text-align: center;
    font-family: "Arimo", Arial, sans-serif; font-weight: 700;
    font-size: 44px; letter-spacing: -1.5px; line-height: 1.1;
    color: var(--ink); text-transform: uppercase;
  }
  .benefit {
    left: 260px; width: 360px; top: 163px; text-align: center;
    font-size: 13px; font-weight: 700;
  }
  .promise {
    left: 360px; width: 190px; top: 219px; text-align: center;
    font-size: 17px; line-height: 1.05; color: var(--gold);
  }
  .guarantee-badge { left: 287px; top: 249px; width: 52px; height: 52px; }
  .count {
    left: 360px; width: 120px; top: 305px; text-align: center;
    font-size: 19px;
  }
  .count small { font-size: 12px; }

  /* right panel */
  .facts { left: 677px; top: 56px; width: 187px; }
  .facts h2 { font-size: 21px; font-weight: 700; line-height: 1.1; }
  .facts .serving { font-size: 9px; font-weight: 700; line-height: 1.3; }
  .facts .rule-thick { border-top: 3px solid var(--ink); margin-top: 4px; }
  .facts .rule { border-top: 1px solid var(--ink); }
  .facts .row {
    display: flex; justify-content: space-between;
    font-size: 8px; padding: 3px 0;
  }
  .facts .blend { font-size: 7.8px; line-height: 1.3; padding: 3px 0 4px; text-align: justify; }
  .facts .blend-head { display: flex; justify-content: space-between; }
  .facts .foot { font-size: 8px; padding: 5px 0 12px; }
  .facts .other { font-size: 7px; line-height: 1.3; }
</style>
</head>
<body>
  <section class="label">
    <div class="directions">
      <p>SUGGESTED USE: As a dietary supplement, take two (2) capsules 1 hour before physical activity, or as directed by your health care professional. Do not exceed two (2) capsules daily.</p>
      <p>CAUTION: Do not exceed recommended dose. This product is not intended for pregnant or nursing mothers, children under the age of 18, or individuals taking prescription drugs. Discontinue use immediately if nausea, sleeplessness, or nervousness occur. Do not take this product if you have a known medical condition including high blood pressure, diabetes, any cardiovascular disorder, heart disease, hyperthyroidism, or are taking anti-depressant medications. If you have questions about the advisability of taking this product, consult your physician prior to use.</p>
      <p class="storage">KEEP OUT OF THE REACH OF CHILDREN. DO NOT USE IF SAFETY SEAL IS DAMAGED OR MISSING. STORE AT ROOM TEMPERATURE.</p>
    </div>
    <div class="fda-note">* These statements have not been evaluated by the Food and Drug Administration. This product is not intended to diagnose, treat, cure or prevent any disease.</div>
    <div class="maker">Manufactured Exclusively For:<br>COMPANY INFO</div>

    <svg class="hero-art" role="img" aria-label="Glowing blue silhouette of a figure's back and shoulder" viewBox="0 0 310 310">
      <defs>
        <radialGradient id="glow" cx="0.55" cy="0.45" r="0.55">
          <stop offset="0" stop-color="#1d4fa8" stop-opacity="0.55"/>
          <stop offset="0.6" stop-color="#0d2a66" stop-opacity="0.3"/>
          <stop offset="1" stop-color="#000" stop-opacity="0"/>
        </radialGradient>
      </defs>
      <rect width="310" height="310" fill="url(#glow)"/>
    </svg>

    <p class="tagline-top">Enhances sexual desire and drive</p>
    <h1 class="brand-name">Velmora Crest</h1>
    <p class="benefit">POWERFUL, LONG LASTING, HARDER ERECTIONS</p>
    <p class="promise">Works in a minutes and last for hours</p>
    <svg class="guarantee-badge" viewBox="0 0 52 52" aria-hidden="true">
      <circle cx="26" cy="26" r="25" fill="var(--badge)"/>
    </svg>
    <p class="count">60 <small>Tablets</small></p>

    <div class="facts">
      <h2>Supplement Facts</h2>
      <p class="serving">Serving Size: 2 Capsules<br>Servings Per Container: 30</p>
      <div class="rule-thick"></div>
      <div class="row"><span>Amount Per Serving</span><span>% Daily Value</span></div>
      <div class="rule"></div>
      <div class="blend">
        <div class="blend-head"><span>VC-Rx™ Proprietary Formula</span><span>1,560 mg &nbsp;†</span></div>
        Horny Goat Weed (herb powder), Maca (herb powder), Macuna Pruriens (L-Dopa), Polypodium Vulgare (herb powder), Yohimbe Bark (herb powder), Saw Palmetto (herb powder), Muira Puama (herb powder), Arginine (L-Arginine hydrochloride), Panax Ginseng (herb powder)
      </div>
      <div class="rule-thick"></div>
      <p class="foot">† % Daily Value not established</p>
      <p class="other">Other Ingredients: Gelatin, Magnesium Stearate, and Calcium Carbonate.</p>
    </div>
  </section>
</body>
</html>
```